Home Baker of cakes, muffins, cookies and pastries.

I am looking for business cards for my home baking business called " Yum Bea-A Treat " - I want them to be super cute and girly, yet simple and modern at the same time. Pastel colours is what I envision with the main colour being baby pink.

```html
<!DOCTYPE html>
<html lang="en">
<head>
<meta charset="utf-8">
<title>Yum Bea-A Treat — Business Cards</title>
<link rel="stylesheet" href="https://fonts.googleapis.com/css2?family=Playfair+Display:ital,wght@0,400;1,400&family=Montserrat:wght@400;600&display=swap">
<style>
  :root {
    --bg: #e9e6e7;
    --card: #ffffff;
    --pink: #ee8aa8;
    --pink-deep: #e97b9d;
    --teal: #93d4d8;
    --white: #ffffff;
    --shadow: rgba(40, 30, 35, 0.18);
  }
  * { box-sizing: border-box; margin: 0; padding: 0; }
  html, body { width: 1200px; height: 900px; overflow: hidden; }
  body {
    background: var(--bg);
    position: relative;
    font-family: "Montserrat", Arial, sans-serif;
  }
  .card {
    position: absolute;
    left: 340px;
    width: 520px;
    height: 300px;
    background: var(--card);
    border-radius: 22px;
    overflow: hidden;
    box-shadow: 0 10px 28px var(--shadow);
  }
  .card--front { top: 110px; }
  .card--back { top: 490px; }
  .card__swoosh { position: absolute; inset: 0; width: 520px; height: 300px; }
  .brand {
    position: absolute;
    left: 0;
    width: 380px;
    top: 82px;
    display: flex;
    align-items: center;
    justify-content: center;
    gap: 12px;
  }
  .brand__dot {
    width: 14px; height: 14px;
    border-radius: 50%;
    background: var(--pink);
  }
  .brand__name {
    font-family: "Playfair Display", Georgia, serif;
    font-weight: 400;
    font-size: 38px;
    color: var(--pink);
    letter-spacing: 0.5px;
    white-space: nowrap;
  }
  .front__web {
    position: absolute;
    left: 250px;
    top: 218px;
    color: var(--white);
    font-weight: 600;
    font-size: 15px;
    letter-spacing: 2.5px;
    transform: rotate(-19deg);
    transform-origin: left center;
    white-space: nowrap;
  }
  .person {
    position: absolute;
    left: 212px;
    top: 222px;
    text-align: right;
    color: var(--white);
    font-family: "Playfair Display", Georgia, serif;
    transform: rotate(-14deg);
    transform-origin: right center;
  }
  .person__name { font-style: italic; font-size: 22px; line-height: 1.1; }
  .person__role { font-size: 15px; }
  .divider {
    position: absolute;
    left: 337px;
    top: 196px;
    width: 2px;
    height: 46px;
    background: var(--white);
    opacity: 0.85;
  }
  .contact {
    position: absolute;
    left: 352px;
    top: 186px;
    list-style: none;
    color: var(--white);
    font-size: 11px;
    line-height: 1.55;
    transform: rotate(-14deg);
    transform-origin: left center;
  }
  .contact li { display: flex; align-items: center; gap: 6px; white-space: nowrap; }
  .contact li.contact__web { font-weight: 600; font-size: 11.5px; }
  .contact svg { width: 10px; height: 10px; flex: none; }
  .contact__bullet { width: 7px; height: 7px; border-radius: 50%; background: var(--white); margin: 0 1.5px; flex: none; }
</style>
</head>
<body>

<section class="card card--front" aria-label="Business card front">
  <svg class="card__swoosh" viewBox="0 0 520 300" aria-hidden="true">
    <path d="M140 300 Q255 150 520 112 L520 126 Q272 162 158 300 Z" fill="var(--teal)"/>
    <path d="M168 300 Q285 170 520 132 L520 300 Z" fill="var(--pink)"/>
  </svg>
  <div class="brand">
    <span class="brand__dot"></span>
    <span class="brand__name">Yum Bea-A Treat</span>
  </div>
  <p class="front__web">www.yumbea-atreat.com</p>
</section>

<section class="card card--back" aria-label="Business card back">
  <svg class="card__swoosh" viewBox="0 0 520 300" aria-hidden="true">
    <path d="M108 300 Q235 140 520 108 L520 120 Q250 152 124 300 Z" fill="var(--teal)"/>
    <path d="M132 300 Q262 160 520 124 L520 300 Z" fill="var(--pink)"/>
  </svg>
  <div class="brand">
    <span class="brand__dot"></span>
    <span class="brand__name">Yum Bea-A Treat</span>
  </div>
  <div class="person">
    <p class="person__name">Clara Mendes</p>
    <p class="person__role">Chef</p>
  </div>
  <span class="divider"></span>
  <ul class="contact">
    <li>
      <svg viewBox="0 0 10 10" aria-hidden="true"><path d="M1 2 Q1 1 2 1 L3 1 L4 3 L3 4 Q4 6 6 7 L7 6 L9 7 L9 8 Q9 9 8 9 Q1 8 1 2 Z" fill="var(--white)"/></svg>
      0400 123 456
    </li>
    <li>
      <svg viewBox="0 0 10 10" aria-hidden="true"><rect x="0.8" y="2" width="8.4" height="6" fill="none" stroke="var(--white)" stroke-width="1"/><path d="M1 2.4 L5 5.5 L9 2.4" fill="none" stroke="var(--white)" stroke-width="1"/></svg>
      clara@yumbea-atreat.com
    </li>
    <li class="contact__web">
      <span class="contact__bullet"></span>
      www.yumbea-atreat.com
    </li>
  </ul>
</section>

</body>
</html>
```